Harborview Estates Business Card for Apartment Buildings

Create business cards for resident managers who run apartment buildings. The audience is the public who are searching for apartment rentals, and current residents who live at the apartment building. Key design element will be incorporating the company logo, however, the logo cannot dominate. The building name and manager name are more important than the logo. Current business card design leaves little room for copy, so we may need to reduce the size on the current card to allow for more space for copy.

Target Market(s)

Adults 18-65 years of age, who are looking for an apartment rental, plus current residents who live at our apartment buildings.

Industry/Entity Type

Property Management

Contact Information for Business Card

A major design element will be use of the company logo. Important property and manager contact information must be part of the design. The size of the logo will need to be reduced to make room for building and manager contact copy.

Font styles to use
Sans Serif

Colors
3176b5
000000
959595
ffffff

Requirements
Must have
• 1) Incorporate the company logo.
• 2) Use the company colors (dark blue, black/grey, over white).
• 3) FEATURE THE BUILDING NAME
• 4) FEATURE THE MANAGER NAME
• 5) The company name is less important than BUILDING and MANAGER
• 6) Manager contact information
• **SEE ATTACHED CREATIVE BRIEF**
Nice to have
• 1) Back of card logo watermark
• 2) Ability to write notes on back of carfd
Should not have
• Avoid letting the company logo dominate the card, the building name and manager are more important than the company logo.

```html
<!DOCTYPE html>
<html lang="en">
<head>
<meta charset="utf-8">
<title>Harborview Estates – Resident Manager Business Card</title>
<link href="https://fonts.googleapis.com/css2?family=Roboto:wght@400;700&display=swap" rel="stylesheet">
<style>
  :root {
    --brand-blue: #0a68a8;
    --brand-grey: #4a4a4c;
    --text-grey: #555555;
    --paper: #ffffff;
    --backdrop: #e9e9ea;
    --watermark: #e6e7ea;
  }
  * { box-sizing: border-box; margin: 0; padding: 0; }
  html, body {
    width: 1200px; height: 960px; overflow: hidden;
    background: var(--backdrop);
    font-family: "Roboto", Arial, sans-serif;
  }
  .card {
    position: absolute; left: 280px; width: 655px; height: 374px;
    background: var(--paper); overflow: hidden;
    box-shadow: 0 2px 6px rgba(0,0,0,0.18);
  }
  .card--front { top: 80px; }
  .card--back { top: 506px; }

  .brand { position: absolute; left: 42px; top: 52px; display: flex; align-items: center; gap: 12px; }
  .brand__dot { width: 26px; height: 26px; border-radius: 50%; background: var(--brand-blue); }
  .brand__name { font-size: 30px; font-weight: 700; color: var(--brand-blue); letter-spacing: 0.2px; }

  .manager { position: absolute; left: 50px; top: 157px; }
  .manager__name { font-size: 22px; font-weight: 700; color: var(--brand-blue); }
  .manager__title { font-size: 15.5px; color: var(--text-grey); margin-top: 4px; }

  .contact-list { position: absolute; left: 50px; top: 246px; list-style: none; }
  .contact-list li {
    display: flex; align-items: center; gap: 9px;
    color: var(--paper); font-size: 15px; height: 22.5px;
  }
  .contact-list svg { width: 15px; height: 15px; flex: none; }

  .property {
    position: absolute; left: 280px; top: 246px;
    color: var(--paper); font-size: 15px; line-height: 22.5px; font-style: normal;
  }
  .property__name { font-weight: 700; }

  .seal { position: absolute; left: 0; top: 0; width: 655px; height: 374px; }
</style>
</head>
<body>

<section class="card card--front" aria-label="Business card front">
  <svg class="seal" viewBox="0 0 655 374" aria-hidden="true">
    <path d="M0 228 H487 L468 353 H0 Z" fill="var(--brand-blue)"/>
    <circle cx="596" cy="305" r="112" fill="var(--paper)"/>
    <circle cx="596" cy="305" r="100" fill="none" stroke="var(--brand-grey)" stroke-width="10"/>
    <circle cx="596" cy="305" r="78" fill="var(--brand-blue)"/>
  </svg>

  <div class="brand">
    <span class="brand__dot"></span>
    <span class="brand__name">Harborview Estates</span>
  </div>

  <div class="manager">
    <h1 class="manager__name">Marisol Quintero</h1>
    <p class="manager__title">Resident Manager</p>
  </div>

  <ul class="contact-list">
    <li>
      <svg viewBox="0 0 16 16" fill="#fff"><path d="M4 1 L6.5 4.5 L5 6.5 C6 8.5 7.5 10 9.5 11 L11.5 9.5 L15 12 L13 15 C7 14.5 1.5 9 1 3 Z"/></svg>
      555-214-3080
    </li>
    <li>
      <svg viewBox="0 0 16 16" fill="#fff"><rect x="1" y="5" width="14" height="7" rx="1.5"/><rect x="4" y="1.5" width="8" height="4" fill="none" stroke="#fff" stroke-width="1.4"/><rect x="4" y="10" width="8" height="5" fill="var(--brand-blue)" stroke="#fff" stroke-width="1.4"/></svg>
      555-214-3091
    </li>
    <li>
      <svg viewBox="0 0 16 16"><rect x="1" y="3.5" width="14" height="9" fill="#fff"/><path d="M1 3.5 L8 9 L15 3.5" fill="none" stroke="var(--brand-blue)" stroke-width="1.3"/></svg>
      555-630-4100
    </li>
    <li>
      <svg viewBox="0 0 16 16" fill="none" stroke="#fff" stroke-width="1.2"><circle cx="8" cy="8" r="6.5"/><ellipse cx="8" cy="8" rx="3" ry="6.5"/><path d="M1.5 8 H14.5 M2.5 4.8 H13.5 M2.5 11.2 H13.5"/></svg>
      marisol@harborviewest.com
    </li>
  </ul>

  <address class="property">
    <div class="property__name">Bayside Villas Apartments</div>
    <div>2485 Linden Avenue</div>
    <div>Fairport, CA 90417</div>
  </address>
</section>

<section class="card card--back" aria-label="Business card back">
  <svg class="seal" viewBox="0 0 655 374" aria-hidden="true">
    <circle cx="327" cy="205" r="125" fill="none" stroke="var(--watermark)" stroke-width="12"/>
  </svg>
</section>

</body>
</html>
```